Every Shelf Set Neatly or ESN Organized needs a business card design. ESN Organized is a professi

We need a business card design that is clean, sharp and conveys a sense of organization. I already have a logo.

Target Market(s)

Families (specifically mothers), small business owners, parents, seniors

Industry/Entity Type

Business

Contact Information for Business Card

My website is www.esnorganized-example.com and my Facebook page is http://www.sociallink-example.com/everyshelfsetneatly. The phone number is 418-552-7094 and I want to be listed as Lorna M. Pelham, Owner

Requirements
Must have
• My logo.

```html
<!DOCTYPE html>
<html lang="en">
<head>
<meta charset="utf-8">
<title>ESN Organized – Business Card</title>
<link rel="stylesheet" href="https://fonts.googleapis.com/css2?family=Open+Sans:wght@400;600&display=swap">
<style>
  :root {
    --page: #ecebe8;
    --card-grey: #e4e4e6;
    --card-light: #f7f7f8;
    --brand-blue: #1a78d6;
    --brand-blue-deep: #1461b3;
    --brand-blue-soft: #5f93c9;
    --ink-grey: #6c6f73;
    --logo-ink: #2b2d31;
    --white: #ffffff;
  }
  html, body {
    margin: 0;
    width: 1200px;
    height: 891px;
    overflow: hidden;
    background: var(--page);
    font-family: "Open Sans", Arial, sans-serif;
  }
  .business-card {
    position: absolute;
    left: 150px;
    top: 188px;
    width: 900px;
    height: 514px;
    border-radius: 14px;
    overflow: hidden;
    background: radial-gradient(ellipse at 55% 20%, var(--card-light), var(--card-grey) 70%);
    box-shadow: 0 10px 30px rgba(0,0,0,.18);
  }
  .card-shapes { position: absolute; inset: 0; }
  .identity {
    position: absolute;
    left: 78px;
    top: 70px;
  }
  .identity__name {
    margin: 0;
    font-size: 38px;
    font-weight: 400;
    letter-spacing: 3px;
    color: var(--brand-blue);
    text-transform: uppercase;
  }
  .identity__role {
    margin: 2px 0 0;
    font-size: 18px;
    font-weight: 400;
    letter-spacing: 5px;
    color: var(--ink-grey);
  }
  .contact-list {
    position: absolute;
    left: 62px;
    top: 238px;
    margin: 0;
    padding: 0;
    list-style: none;
    color: var(--white);
  }
  .contact-list li {
    display: flex;
    align-items: center;
    gap: 16px;
    height: 36px;
    font-size: 21px;
    font-weight: 400;
  }
  .contact-list li.contact--social { font-size: 16px; }
  .contact-list svg { width: 20px; height: 24px; flex: none; }
  .logo-panel {
    position: absolute;
    left: 598px;
    top: 150px;
    width: 290px;
    height: 200px;
    border-radius: 18px;
    background: radial-gradient(ellipse at 50% 45%, var(--white), #e9e9ec 80%);
    box-shadow: 0 4px 12px rgba(0,0,0,.12);
    display: flex;
    align-items: center;
    justify-content: center;
  }
  .logo-panel__name {
    font-size: 30px;
    font-weight: 400;
    letter-spacing: 3px;
    color: var(--logo-ink);
  }
  .brand-name-footer {
    position: absolute;
    right: 62px;
    bottom: 62px;
    font-size: 40px;
    font-weight: 400;
    letter-spacing: 2px;
    color: var(--white);
    line-height: 1;
  }
</style>
</head>
<body>
  <article class="business-card">
    <svg class="card-shapes" viewBox="0 0 900 514" preserveAspectRatio="none" aria-hidden="true">
      <polygon points="0,218 560,218 590,250 620,230 900,230 900,514 0,514" fill="var(--brand-blue)"/>
      <polygon points="548,180 606,180 606,320 578,300" fill="var(--brand-blue-soft)"/>
      <rect x="0" y="480" width="900" height="34" fill="var(--brand-blue-deep)"/>
    </svg>

    <header class="identity">
      <h1 class="identity__name">Lorna M. Pelham</h1>
      <p class="identity__role">Owner</p>
    </header>

    <ul class="contact-list">
      <li>
        <svg viewBox="0 0 20 24"><rect x="4" y="1" width="12" height="22" rx="2.5" fill="var(--white)"/><rect x="6.5" y="4" width="7" height="12" fill="var(--brand-blue)"/></svg>
        418 - 552 - 7094
      </li>
      <li>
        <svg viewBox="0 0 20 24"><rect x="0" y="6" width="20" height="13" rx="1.5" fill="var(--white)"/><polyline points="1,7 10,14 19,7" fill="none" stroke="var(--brand-blue)" stroke-width="1.8"/></svg>
        www.esnorganized-example.com
      </li>
      <li class="contact--social">
        <svg viewBox="0 0 20 24"><g fill="none" stroke="var(--white)" stroke-width="2.2" stroke-linecap="round"><rect x="1.5" y="10" width="10" height="6" rx="3" transform="rotate(-40 6.5 13)"/><rect x="8.5" y="8" width="10" height="6" rx="3" transform="rotate(-40 13.5 11)"/></g></svg>
        www.sociallink-example.com/everyshelfsetneatly
      </li>
    </ul>

    <div class="logo-panel">
      <span class="logo-panel__name">ESN Organized</span>
    </div>

    <div class="brand-name-footer">ESN Organized</div>
  </article>
</body>
</html>
```